Hi,
We are also sourcing for a logo, if you have ideas please take a look at our other project (if you look at our profile you should be able to see it).
We are looking for a website that will be used to manage mobile devices. The feature set is rather small, users can Wipe, Lock, Locate devices as well as make them Ring or Speak (by sending text to be spoken). We attached some images of what it looks like right now. We are looking for simplicity, uniformity and most importantly, the website should be thought of as primary User Interface, it should flow.
Please see attached to get an idea of what it looks like now. The current design was inspired by making a site that will work and flow well on a variety of displays (from mobile to tablet to desktop).
We want to stay away from radio buttons, check-boxes. This should be engaging and creative, opposite of Corporate. Not busy (ideally we are looking to have fewest possible choices at any given time and at the same time no feature should be more than 3 clicks away (this is a suggestion/approximation... just want to share our understanding of what 'flow' is).
Could be cartoony.
Thanks!
BrisketLoom
Reason: there are a couple of designs that are interesting, in addition to specific feedback I provided, possibly looking for more concepts.
Thank You

```html
<!DOCTYPE html>
<html lang="en">
<head>
<meta charset="utf-8">
<title>BrisketLoom – Lost Your Phone</title>
<link rel="stylesheet" href="https://fonts.googleapis.com/css2?family=Poiret+One&family=Arimo:wght@400&family=Open+Sans:wght@700&display=swap">
<style>
:root{
  --black:#000;
  --orange:#e97d06;
  --orange-band:rgba(120,60,0,.18);
  --ink:#1b1b1b;
  --white:#fff;
  --paper:#f7f6f2;
  --frame:#e2e0da;
  --grey-badge:#7a7a7a;
  --muted:#8a8a8a;
}
*{margin:0;padding:0;box-sizing:border-box}
html,body{width:1200px;height:1150px;overflow:hidden;background:var(--paper)}
body{position:relative;font-family:"Arimo",Arial,sans-serif;color:var(--ink)}
.thin{font-family:"Poiret One",sans-serif}

.site-header{position:absolute;left:0;top:0;width:1200px;height:60px;background:var(--black)}
.brand{position:absolute;left:142px;top:6px;font-family:"Poiret One",sans-serif;font-size:42px;color:var(--white);letter-spacing:-.5px}
.main-nav{position:absolute;left:652px;top:15px;display:flex}
.main-nav a{font-family:"Poiret One",sans-serif;font-size:19px;color:var(--white);text-decoration:none;height:34px;line-height:34px;padding:0 13px;border-radius:17px;font-weight:bold}
.main-nav a.active{background:var(--orange)}
.main-nav a+a{margin-left:3px}

.hero{position:absolute;left:0;top:60px;width:1200px;height:451px;
  background:radial-gradient(ellipse 260px 120px at 520px 0,#f6c88c 0%,rgba(246,200,140,0) 100%),linear-gradient(180deg,#ef8d14,var(--orange) 60%,#e37504)}
.hero-band{position:absolute;left:0;top:68px;width:1200px;height:62px;background:var(--orange-band)}
.hero-title{position:absolute;left:155px;top:64px;font-size:56px;color:var(--white);font-weight:bold;word-spacing:6px}
.hero-copy{position:absolute;left:157px;top:146px;font-size:15px;line-height:30px;color:#1a1208}
.cta{position:absolute;left:155px;top:253px;width:297px;height:53px;background:#111;border:2px solid #f8b35c;border-radius:3px;box-shadow:0 0 6px rgba(255,220,170,.6)}
.cta-label{position:absolute;left:15px;top:12px;font-family:"Open Sans",sans-serif;font-weight:700;font-size:20px;color:var(--white)}
.cta svg{position:absolute;right:0;top:0}
.hero-steps{position:absolute;left:160px;top:342px;font-size:24px;color:#1a1208;font-weight:bold;word-spacing:3px}
.device-visual{position:absolute;left:652px;top:90px;width:423px;height:545px;border-radius:46px;z-index:2;
  background:linear-gradient(180deg,#3a3a3a 0%,#1a1a1a 70%,rgba(220,220,220,.4) 100%)}

.welcome{position:absolute;left:0;top:511px;width:1200px;height:122px;background:var(--white);box-shadow:0 6px 8px -6px rgba(0,0,0,.25)}
.welcome h2{position:absolute;left:158px;top:12px;font-size:42px;font-weight:bold;color:var(--ink)}
.welcome p{position:absolute;left:166px;top:70px;font-size:15px;line-height:18px;width:420px}

.photo{position:absolute;border:1px solid var(--frame);background:var(--white);padding:5px;width:261px;height:193px}
.photo div{width:100%;height:100%}
.feature-title{position:absolute;font-size:29px;font-weight:bold;white-space:nowrap;color:var(--ink)}
.ticks{position:absolute;list-style:none;font-size:15px;line-height:24px;white-space:nowrap}
.ticks li{position:relative;padding-left:22px}
.ticks li.tick::before{content:"";position:absolute;left:2px;top:7px;width:10px;height:5px;border-left:1.5px solid #222;border-bottom:1.5px solid #222;transform:rotate(-48deg)}

.store-name{position:absolute;left:807px;top:924px;display:flex;align-items:center;gap:12px;font-size:28px;color:var(--muted)}
.store-name span.mark{width:40px;height:40px;background:var(--muted)}
.store-badge{position:absolute;left:817px;top:990px;width:201px;height:63px;border-radius:7px;background:var(--grey-badge)}

.site-footer{position:absolute;left:0;top:1088px;width:1200px;height:62px;background:var(--black)}
.foot-nav{position:absolute;left:153px;top:20px;display:flex;gap:22px}
.foot-nav a{font-family:"Poiret One",sans-serif;font-size:15px;font-weight:bold;color:var(--white);text-decoration:none}
.copyright{position:absolute;left:852px;top:12px;font-size:12px;color:var(--white)}
.social{position:absolute;left:942px;top:37px;display:flex;gap:5px}
.social span{width:19px;height:19px;background:var(--orange);border-radius:2px}
</style>
</head>
<body>
<header class="site-header">
  <div class="brand">BrisketLoom</div>
  <nav class="main-nav">
    <a class="active" href="#">Home</a><a href="#">About</a><a href="#">Get Application</a><a href="#">Contact</a>
  </nav>
</header>

<section class="hero">
  <div class="hero-band"></div>
  <h1 class="hero-title thin">Lost Your Phone</h1>
  <p class="hero-copy">Lorem ipsum dolor sit amet, consectetur adipiscing elit.<br>Mauris id erat non nibh semper tincidunt id eu massa.<br>Quisque sit amet nibh sit amet erat tincidunt mollis.</p>
  <a class="cta" href="#">
    <span class="cta-label">Get the Application</span>
    <svg width="70" height="49" viewBox="0 0 70 49" aria-hidden="true">
      <path d="M0 24.5 L28 0 H70 V49 H28 Z" fill="#fff"/>
      <rect x="28" y="10" width="29" height="29" rx="3" fill="#f07f0a"/>
      <path d="M42.5 18 V29 M38.5 25 L42.5 29.5 L46.5 25" stroke="#fff" stroke-width="2" fill="none"/>
    </svg>
  </a>
  <div class="hero-steps thin">LOST -- RING -- WIPE IT -- FIND IT</div>
</section>

<div class="device-visual" role="img" aria-label="Two smartphones: one showing a phone being slipped from a jeans pocket, the other showing a location map with a pin"></div>

<section class="welcome">
  <h2 class="thin">Welcome to</h2>
  <p>Find out whats hapenning, right now with the mobile services you care about</p>
</section>

<div class="photo" style="left:146px;top:649px"><div role="img" aria-label="Hand taking a phone out of a jeans pocket" style="background:linear-gradient(135deg,#3f5d85,#6d87a8 60%,#e8e6e2)"></div></div>
<h3 class="feature-title thin" style="left:146px;top:858px">Lost or stolen phone?</h3>
<ul class="ticks" style="left:146px;top:906px">
  <li class="tick">Find your phone when you need it</li>
  <li class="tick">must by maps on ringer</li>
  <li>Remotely wipe your conditional data</li>
  <li class="tick">Register your Stolen Phone</li>
</ul>

<div class="photo" style="left:469px;top:655px"><div role="img" aria-label="Toy bear holding a phone beside a laptop" style="background:linear-gradient(135deg,#f4f4f4,#d8d8d8 60%,#9a9a9a)"></div></div>
<h3 class="feature-title thin" style="left:474px;top:857px">Protect and Secure</h3>
<ul class="ticks" style="left:473px;top:907px">
  <li class="tick">Monitor instant messaging like SMS</li>
  <li class="tick">Record Voice commentaries</li>
  <li class="tick">Camera Observation</li>
  <li class="tick">Get notified if your child is skipping<br>class</li>
  <li class="tick">backup share your pictures and<br>contacts</li>
</ul>

<div class="photo" style="left:791px;top:657px"><div role="img" aria-label="Hand holding a smartphone on a blue background" style="background:linear-gradient(135deg,#0a3b86,#0b2f70 60%,#c9a58a)"></div></div>
<h3 class="feature-title thin" style="left:795px;top:857px">Apps</h3>
<div class="store-name"><span class="mark"></span>Pocket Market</div>
<div class="store-badge" role="img" aria-label="App store listing badge"></div>

<footer class="site-footer">
  <nav class="foot-nav"><a href="#">Home</a><a href="#">About</a><a href="#">Get Application</a><a href="#">Contact</a></nav>
  <div class="copyright">© 2012.www.brisketloom.com</div>
  <div class="social"><span></span><span></span><span></span></div>
</footer>
</body>
</html>
```